BOLD & MINIMALIST DESIGN NEEDED

We want a very bold but minimalistic business card design that is impactful and utilizes both sides of the business card. Our current logo is included for your use.

We want bold fonts and good use of negative space. We don't want the logo to overpower the design.

Target Market(s)

Professionals who are building new commercial buildings.

Industry/Entity Type

Construction

Contact Information for Business Card

Name, Title, email, office phone, cell phone, website

Font styles to use
Serif
Sans Serif

Requirements
Must have
• Bold design!

```html
<!DOCTYPE html>
<html lang="en">
<head>
<meta charset="utf-8">
<title>Ridgeline Design + Build — Business Card</title>
<link href="https://fonts.googleapis.com/css2?family=Open+Sans:wght@400;600;700;800&display=swap" rel="stylesheet">
<style>
  :root {
    --canvas: #ececec;
    --paper: #ffffff;
    --ink: #1a1a1a;
    --black: #0b0b0b;
    --black-soft: #2a2a2a;
    --green: #7cc242;
    --green-light: #a6da6e;
    --grey: #6f6f6f;
    --rule: #4a4a4a;
  }
  * { box-sizing: border-box; margin: 0; padding: 0; }
  html, body {
    width: 1200px; height: 900px; overflow: hidden;
    background: var(--canvas);
    font-family: "Open Sans", Arial, sans-serif;
  }
  .sheet {
    position: relative; width: 1200px; height: 900px;
    display: flex; align-items: center; justify-content: center; gap: 50px;
  }
  .card {
    position: relative; width: 540px; height: 310px;
    border-radius: 18px; overflow: hidden;
    box-shadow: 0 14px 30px rgba(0,0,0,.22);
  }

  /* Front */
  .card--front { background: var(--paper); color: var(--ink); }
  .contact-block { position: absolute; left: 34px; top: 38px; width: 240px; }
  .person-name {
    font-weight: 700; font-size: 21px; color: var(--green);
    letter-spacing: .3px; text-transform: uppercase;
  }
  .person-title { font-size: 13px; color: var(--grey); margin-top: 2px; }
  .divider { height: 1px; background: var(--rule); margin: 10px 0 12px; }
  .contact-list { list-style: none; }
  .contact-list li {
    display: flex; align-items: center; gap: 7px;
    font-size: 13px; color: var(--black-soft); line-height: 21px;
  }
  .contact-list svg { width: 11px; height: 11px; flex: none; }

  .brand-block { position: absolute; right: 34px; top: 92px; width: 230px; text-align: right; }
  .brand-name {
    font-weight: 800; font-size: 22px; color: var(--ink);
    text-transform: uppercase; line-height: 1.1;
    display: flex; align-items: center; justify-content: flex-end; gap: 8px;
  }
  .brand-mark { width: 14px; height: 14px; background: var(--green); flex: none; }
  .brand-rule { height: 1px; background: var(--rule); margin-top: 14px; }

  .address {
    position: absolute; right: 34px; top: 196px;
    font-size: 15px; color: var(--grey); text-align: right; line-height: 1.35;
  }

  .edge-band { position: absolute; left: 0; bottom: 0; width: 100%; height: 30px; }

  /* Back */
  .card--back {
    background: radial-gradient(circle at 30% 20%, #2b2b2b 0%, var(--black) 65%);
    display: flex; align-items: center; justify-content: center;
  }
  .back-brand { text-align: center; }
  .back-brand .brand-name {
    color: #ffffff; font-size: 30px; justify-content: center;
  }
  .back-brand .brand-rule { background: #ffffff; margin: 12px auto 0; width: 100%; }
</style>
</head>
<body>
<main class="sheet">
  <section class="card card--front" aria-label="Card front">
    <div class="contact-block">
      <p class="person-name">Marcus Hale</p>
      <p class="person-title">Managing Director</p>
      <div class="divider"></div>
      <ul class="contact-list">
        <li>
          <svg viewBox="0 0 12 12" aria-hidden="true"><circle cx="6" cy="6" r="6" fill="var(--green)"/><path d="M3.6 3.2l1.3-.3.7 1.5-.8.6c.4.9 1 1.5 1.9 1.9l.6-.8 1.5.7-.3 1.3C6 8.1 3.9 6 3.6 3.2z" fill="#fff"/></svg>
          044-555 218 460
        </li>
        <li>
          <svg viewBox="0 0 12 12" aria-hidden="true"><circle cx="6" cy="6" r="6" fill="var(--green)"/><rect x="3" y="3.8" width="6" height="4.4" fill="#fff"/><path d="M3 3.8l3 2.4 3-2.4" stroke="var(--green)" stroke-width=".8" fill="none"/></svg>
          info@ridgelinebuild.com
        </li>
        <li>
          <svg viewBox="0 0 12 12" aria-hidden="true"><circle cx="6" cy="6" r="6" fill="var(--green)"/><circle cx="6" cy="6" r="3" fill="none" stroke="#fff" stroke-width=".8"/><path d="M3 6h6M6 3c-1.2 1.6-1.2 4.4 0 6M6 3c1.2 1.6 1.2 4.4 0 6" stroke="#fff" stroke-width=".6" fill="none"/></svg>
          www.ridgelinebuild.com
        </li>
      </ul>
    </div>

    <div class="brand-block">
      <p class="brand-name"><span class="brand-mark"></span>Ridgeline Design + Build</p>
      <div class="brand-rule"></div>
    </div>

    <p class="address">Your Address, City<br>State, Zip 0000</p>

    <svg class="edge-band" viewBox="0 0 540 30" preserveAspectRatio="none" aria-hidden="true">
      <polygon points="0,0 200,0 216,30 0,30" fill="var(--black)"/>
      <polygon points="200,0 540,0 540,30 216,30" fill="var(--green)"/>
      <polygon points="200,0 540,0 540,8 204,8" fill="var(--green-light)"/>
    </svg>
  </section>

  <section class="card card--back" aria-label="Card back">
    <div class="back-brand">
      <p class="brand-name">Ridgeline Design + Build</p>
      <div class="brand-rule"></div>
    </div>
  </section>
</main>
</body>
</html>
```